Elmhollow Restaurnt Lunch Menu Redesign:

We have two lunch special menus that need to be reformatted into a 4.25inx11in and need a graphics design update. Some menu items need to change and some descriptions need to updated. This new menu should double sided with the Main Dining Lunch Menu on the front side and Teppanyaki Lunch menu on the back.

Both menus should follow the same design formatting as the main dining lunch menu (font, sizing, ect.)

```html
<!DOCTYPE html>
<html lang="en">
<head>
<meta charset="utf-8">
<title>Elmhollow Restaurnt — Lunch Menu</title>
<link rel="stylesheet" href="https://fonts.googleapis.com/css2?family=DM+Serif+Display&family=Montserrat:wght@600&family=Open+Sans:ital,wght@0,400;0,700;1,400&display=swap">
<style>
  :root {
    --canvas: #ffffff;
    --page: #ffffff;
    --ink: #1c1c1c;
    --muted: #555555;
    --band: #2d2d2d;
    --band-text: #ffffff;
    --stripe: #f5f5f5;
    --stripe-strong: #eeeeee;
    --rule: #555555;
  }
  * { box-sizing: border-box; margin: 0; padding: 0; }
  html, body { width: 932px; height: 1200px; overflow: hidden; background: var(--canvas); }
  body { position: relative; font-family: "Open Sans", sans-serif; color: var(--ink); }

  .menu-page {
    position: absolute; top: 129px; width: 399px; height: 1033px;
    background: var(--page);
    box-shadow: 0 6px 22px rgba(0,0,0,0.12);
  }
  .menu-page--front { left: 45px; }
  .menu-page--back { left: 486px; }

  .menu-title {
    position: absolute; top: 20px; left: 0; width: 100%;
    text-align: center; font-family: "DM Serif Display", serif;
    font-size: 35px; line-height: 42px; letter-spacing: -0.3px;
  }
  .hours {
    position: absolute; top: 66px; left: 105px; width: 189px; height: 17px;
    display: flex; align-items: center; justify-content: center;
  }
  .hours::before {
    content: ""; position: absolute; left: 0; right: 0; top: 8px;
    border-top: 1px solid var(--ink);
  }
  .hours__badge {
    position: relative; background: var(--ink); color: #fff;
    font-family: "Montserrat", sans-serif; font-weight: 600; font-size: 9.5px;
    padding: 0 6px; height: 17px; line-height: 17px; border-radius: 4px;
  }

  .section-band {
    position: absolute; left: 38px; width: 322px; height: 29px;
    background: var(--band); color: var(--band-text);
    font-family: "DM Serif Display", serif; font-size: 17.5px;
    line-height: 29px; text-align: center;
  }
  .section-note {
    position: absolute; left: 38px; width: 322px; text-align: center;
    font-size: 6.6px; line-height: 8.3px; color: var(--ink);
  }

  .item {
    position: absolute; left: 38px; width: 322px; height: 21px;
    display: flex; align-items: center; justify-content: space-between;
    padding: 0 8px 0 2px;
  }
  .item--tall { height: 33px; }
  .item--striped { background: var(--stripe); }
  .item--strong { background: var(--stripe-strong); }
  .item__name { font-size: 12px; line-height: 12.5px; }
  .item__name em { font-style: italic; font-size: 9.3px; color: var(--muted); }
  .item__desc { display: block; font-style: italic; font-size: 9.3px; line-height: 11px; color: var(--muted); }
  .item__price { font-size: 11px; color: var(--muted); white-space: nowrap; }

  .sushi {
    position: absolute; width: 138px; height: 22px;
    display: flex; align-items: center; padding-left: 2px;
    font-size: 12px;
  }
  .sushi em { font-style: italic; font-size: 9.3px; margin-left: 3px; }
  .sushi--left { left: 38px; }
  .sushi--right { left: 222px; }
  .sushi--striped { background: var(--stripe); }
  .sushi--indent { padding-left: 8px; left: 223px; }
  .sushi-divider {
    position: absolute; left: 222px; top: 506px; width: 0; height: 90px;
    border-left: 1.3px solid var(--rule);
  }

  .fine-print {
    position: absolute; left: 0; width: 100%; top: 991px;
    text-align: center; font-size: 8.6px; line-height: 11px;
  }
  .fine-print strong { font-style: normal; }
  .fine-print em { font-style: italic; }
</style>
</head>
<body>

<section class="menu-page menu-page--front" aria-label="Main dining lunch menu">
  <h1 class="menu-title">Lunch Specials</h1>
  <div class="hours"><span class="hours__badge">Served Daily 11AM - 3PM</span></div>

  <h2 class="section-band" style="top:115px">Sandwiches</h2>
  <p class="section-note" style="top:150px">Served with Choice of Miso Soup or House Salad &amp; Potato Chips</p>

  <div class="item item--tall" style="top:173px"><span class="item__name">Fried Breaded Calamari Steak<span class="item__desc">with Tomato, Lettuce &amp; Onion</span></span><span class="item__price">$ 16</span></div>
  <div class="item item--tall item--striped" style="top:211px"><span class="item__name">Grilled Chicken <em>with Bacon, Tomato,</em><span class="item__desc">Lettuce &amp; Mayonnaise Drizzle</span></span><span class="item__price">$ 16</span></div>
  <div class="item item--tall" style="top:248px"><span class="item__name">Hamburger <em>with Lettuce, Tomato,</em><span class="item__desc">Onion, Mayonnaise Drizzle</span></span><span class="item__price">$ 18</span></div>
  <div class="item item--tall item--striped" style="top:286px"><span class="item__name">Fried Soft Shell Crab Burger<span class="item__desc">with Avocado, Lettuce, Tomato, Onion &amp; Mayo</span></span><span class="item__price">$ 20</span></div>

  <h2 class="section-band" style="top:365px">Sushi Specials</h2>
  <p class="section-note" style="top:399px">Please Select 4 of the followings for $16<br>Served with a 4 piece California Roll &amp; Miso Soup or House Salad</p>

  <div class="sushi sushi--left" style="top:430px">Hamachi <em>Yellowtail Tuna</em></div>
  <div class="sushi sushi--left sushi--striped" style="top:456px">Hotate <em>Yellowtail</em></div>
  <div class="sushi sushi--left" style="top:482px">Ika <em>Squid</em></div>
  <div class="sushi sushi--left sushi--striped" style="top:508px">Ikura <em>Salmon Roe</em></div>
  <div class="sushi sushi--left" style="top:533px">Saba <em>Mackerel</em></div>
  <div class="sushi sushi--left sushi--striped" style="top:559px">Sake <em>Salmon</em></div>
  <div class="sushi sushi--left" style="top:585px">Tai <em>Red Snapper</em></div>

  <div class="sushi sushi--right" style="top:430px">Maguro <em>Yellowtail Tuna</em></div>
  <div class="sushi sushi--right sushi--striped" style="top:456px">Smoked Salmon</div>
  <div class="sushi-divider"></div>
  <div class="sushi sushi--indent" style="top:500px">Tako <em>Octopus</em></div>
  <div class="sushi sushi--indent" style="top:526px">Unagi <em>BBQ Eel</em></div>
  <div class="sushi sushi--indent" style="top:551px">Ebi <em>Shrimp</em></div>
  <div class="sushi sushi--indent" style="top:577px">Tamago <em>Egg</em></div>

  <h2 class="section-band" style="top:629px">Main Courses</h2>
  <p class="section-note" style="top:663px">Served with Rice &amp; Choice of Miso Soup or House Salad<br>All Meals Served with Rice. Upgrade to fried rice for only $4</p>

  <div class="item item--tall" style="top:689px"><span class="item__name">Organic Tofu Teriyaki<span class="item__desc">Served Grilled or Tempura Fried</span></span><span class="item__price">$ 14</span></div>
  <div class="item item--striped" style="top:724px"><span class="item__name">Chicken Teriyaki</span><span class="item__price">$ 16</span></div>
  <div class="item" style="top:750px"><span class="item__name">Spicy Chicken Teriyaki</span><span class="item__price">$ 16</span></div>
  <div class="item item--striped" style="top:776px"><span class="item__name">Beef Teriyaki</span><span class="item__price">$ 16</span></div>
  <div class="item" style="top:802px"><span class="item__name">Spicy Beef Teriyaki</span><span class="item__price">$ 16</span></div>
  <div class="item item--tall item--striped" style="top:828px"><span class="item__name">Chicken Kats<span class="item__desc">Breaded Chicken Breast</span></span><span class="item__price">$ 15</span></div>
  <div class="item item--tall" style="top:865px"><span class="item__name">Katsu Don<span class="item__desc">Fried Chicken Breast, Egg &amp; Onion over Rice</span></span><span class="item__price">$ 16</span></div>
  <div class="item item--tall item--striped" style="top:903px"><span class="item__name">Unagi Don<span class="item__desc">BBQ Eel over Rice</span></span><span class="item__price">$ 19</span></div>
  <div class="item" style="top:938px"><span class="item__name">Shrimp &amp; Vegetable Tempura</span><span class="item__price">$ 16</span></div>

  <p class="fine-print"><strong>Served Raw:</strong> <em>20% gratuity added to parties of 6 or more.</em><br><em>Consuming raw or undercooked food may increase your risk of foodborne illness</em></p>
</section>

<section class="menu-page menu-page--back" aria-label="Teppanyaki lunch menu">
  <h2 class="section-band" style="top:33px">Teppanyaki Lunch</h2>
  <p class="section-note" style="top:68px">(Available until 11-2:30pm)<br>Served with Miso Soup or Salad, Choice of Rice &amp; Vegetables</p>

  <div class="item" style="top:91px"><span class="item__name">Hibachi Chicken</span><span class="item__price">$ 18</span></div>
  <div class="item item--striped" style="top:117px"><span class="item__name">Hibachi Shrimp</span><span class="item__price">$ 19</span></div>
  <div class="item" style="top:142px"><span class="item__name">Hibachi New York Steak</span><span class="item__price">$ 20</span></div>
  <div class="item item--striped" style="top:168px"><span class="item__name">Hibachi Salmon</span><span class="item__price">$ 20</span></div>
  <div class="item" style="top:194px"><span class="item__name">Teriyaki Beef</span><span class="item__price">$ 19</span></div>
  <div class="item item--striped" style="top:220px"><span class="item__name">Hibachi Scallop</span><span class="item__price">$ 20</span></div>
  <div class="item" style="top:246px"><span class="item__name">Chicken and Shrimp</span><span class="item__price">$ 21</span></div>
  <div class="item item--striped" style="top:271px"><span class="item__name">Scallop and Shrimp</span><span class="item__price">$ 22</span></div>
  <div class="item" style="top:297px"><span class="item__name">New York Steak and Chicken</span><span class="item__price">$ 22</span></div>
  <div class="item item--striped" style="top:323px"><span class="item__name">New York Steak and Shrimp</span><span class="item__price">$ 23</span></div>
  <div class="item" style="top:349px"><span class="item__name">New York Steak and Scallop</span><span class="item__price">$ 24</span></div>
  <div class="item item--striped" style="top:375px"><span class="item__name">Filet Mignon</span><span class="item__price">$ 23</span></div>
  <div class="item" style="top:400px"><span class="item__name">Filet Mignon and Chicken</span><span class="item__price">$ 25</span></div>
  <div class="item item--striped" style="top:426px"><span class="item__name">Filet Mignon and Shrimp</span><span class="item__price">$ 26</span></div>
  <div class="item" style="top:452px"><span class="item__name">Filet Mignon and Scallop</span><span class="item__price">$ 27</span></div>

  <h2 class="section-band" style="top:531px">Special Menu</h2>
  <p class="section-note" style="top:565px">Ages 12 and Under ~ Ages 65 and Older<br>Served with Miso Soup or Salad, Choice of Rice &amp; Vegetables</p>

  <div class="item" style="top:590px"><span class="item__name">Hibachi Chicken</span><span class="item__price">$ 15</span></div>
  <div class="item item--strong" style="top:616px"><span class="item__name">Hibachi Shrimp</span><span class="item__price">$ 16</span></div>
  <div class="item" style="top:642px"><span class="item__name">Hibachi New York Steak</span><span class="item__price">$ 18</span></div>
  <div class="item item--strong" style="top:668px"><span class="item__name">Hibachi Scallop</span><span class="item__price">$ 18</span></div>
  <div class="item" style="top:694px"><span class="item__name">Teriyaki Beef</span><span class="item__price">$ 16</span></div>
</section>

</body>
</html>
```